I need a business card design for a new dance business. I offer classical Indian dance tuition and also professional performances. I want to offer the community a variety of Indian dance experiences which include: group class and private tuition, school and preschool educational courses and workshops. dance theatre performances, community function workshops and performances, Kids Bollywood parties, wedding & conference performances, mouth percussion classes, Indian mythology/ dance costume and make up workshops.
The final design should communicate a feeling and impression of the vibrance and energy of Indian dance.
Updates
Hi Everyone,
Project Deadline Extended
Reason: I would like to refine a few changes to the details of this lovely design and we have run out of time!
Project Deadline Extended
Reason: Still waiting to hear back form designer re two possible changes to the card design. Tomorrow is the deadline and I have sent several messages but with no response. I need to see this through before selecting this lovely design.
Thank you.
Tara
Industry/Entity Type
Preschool
Requirements
Must have
- The front of the business card should have the photo of me (my face and torso), surrounded entirely by a border of bright magenta (to match the magenta of my lipstick - it is the same as the magenta on my skirt in the second photo). Within the top border I want (perhaps yellow-gold) writing to say "Tara Holloway - Artistic Director" and within the bottom border it should read "Saffron Lantern Indian Dance." If you turn the card on its side the left border should have my telephone number: 0417 862 493 and the right-hand border should read: saffronlanternindiandance@quillmail.example
The reverse of the card should be the orange of the dance costume
and I'd like the picture of my feet and legs to be on the right side of the back of the card as a side border. Centre-aligned on the orange background it should read (perhaps in dark magenta):
Indian dance classes + private tuition
School + preschool educational courses and workshops
Dance theatre performances
Community function workshops and performances
Children's Bollywood parties
Wedding + conference performances
Mouth percussion classes
Indian mythology and dance demonstration workshops
Dance costume and make-up workshops
Nice to have
- A lovely artistic but easy-to-read font would be nice.

```html
<!DOCTYPE html>
<html lang="en">
<head>
<meta charset="utf-8">
<title>Saffron Lantern Indian Dance – Business Card Reverse</title>
<link rel="stylesheet" href="https://fonts.googleapis.com/css2?family=Delius&family=Pinyon+Script&display=swap">
<style>
  :root {
    --page-bg: #ffffff;
    --saffron: #e2761c;
    --magenta-ink: #6b1838;
    --gold-script: #f6c987;
    --photo-silk: #8e1f8f;
    --photo-gold: #d9962e;
    --photo-stone: #b9b3a6;
  }
  html, body {
    margin: 0;
    padding: 0;
    width: 1200px;
    height: 900px;
    overflow: hidden;
    background: var(--page-bg);
  }
  .card {
    position: absolute;
    left: 40px;
    top: 90px;
    width: 1120px;
    height: 710px;
    display: flex;
  }
  .card__panel {
    position: relative;
    width: 846px;
    height: 100%;
    background: var(--saffron);
  }
  .services {
    list-style: none;
    margin: 0;
    padding: 0;
    position: absolute;
    top: 76px;
    left: 0;
    width: 100%;
    text-align: center;
    font-family: "Delius", sans-serif;
    font-size: 28px;
    line-height: 48.6px;
    color: var(--magenta-ink);
    letter-spacing: 0.3px;
  }
  .business-name {
    position: absolute;
    left: 0;
    width: 100%;
    top: 612px;
    margin: 0;
    text-align: center;
    font-family: "Pinyon Script", cursive;
    font-weight: 400;
    font-size: 48px;
    color: var(--gold-script);
    letter-spacing: 1px;
  }
  .card__photo {
    width: 274px;
    height: 100%;
    background: linear-gradient(160deg, var(--photo-stone) 0%, var(--photo-silk) 35%, var(--photo-gold) 60%, var(--photo-silk) 78%, var(--photo-stone) 100%);
  }
</style>
</head>
<body>
  <div class="card">
    <section class="card__panel">
      <ul class="services">
        <li>Indian dance classes + private tuition</li>
        <li>School + preschool educational courses and workshops</li>
        <li>Dance theatre performances</li>
        <li>Community function workshops and performances</li>
        <li>Children's Bollywood parties</li>
        <li>Wedding + conference performances</li>
        <li>Mouth percussion classes</li>
        <li>Indian mythology and dance demonstration workshops</li>
        <li>Dance costume and make-up workshops</li>
      </ul>
      <p class="business-name">Saffron Lantern Indian Dance</p>
    </section>
    <div class="card__photo" role="img" aria-label="Photograph of a dancer's legs and hennaed feet in a magenta silk costume with gold borders and ankle bells"></div>
  </div>
</body>
</html>
```